Exciting opportunity to create logo and a label for our natural health brand.

About us

We are a customer centric health supplement brand who believes in natural medicine and high quality ingredients. We take a holistic approach to healthcare, with an eastern philosophy. We believe in being partners with our customers in their health care journey and are invested in their well being.

Our brand philosophy and values are attached (see Vorna philosophy.png). Our personality traits are:

- Natural
- Fresh
- Modern
- Balanced (in a holistic sense)

Task breakdown

1. Design a fresh feeling logo for us
- We want it to represent our values and high quality ingredients. We would like the quality of the product to be reflected in the branding and have a high end feel.
- Logo text must include Vorna Health Sciences
- We want the Vorna to be the focus of the logo (see uploaded image Vorna logo example.png)
The logo does not have to follow this layout, but we just want the Vorna to stand out. Feel free to use your creative license on this!

2. Create an attractive label to go on the supplement bottle
- The designs need to be eye catching, give a sense of high end ingredients and natural products and tie in with the logo to give a joined up feel.
- We are selling our products online and need them to really stand out from the competition.
- See examples of labels and packaging we like (1 -7 label design).

The initial label we would like you to design would be for our product Calm Drift. It is a product that assists in the management of Anxiety and stress. The label will appear on the bottle that holds the capsules for this supplement, see uploaded files (Example plain bottles.png). The bottles may be white as the picture shows or dark blue recyclable plastic or dark brown glass . We don't have the exact dimensions of the bottle yet, but I will follow up with these.

The label needs to include the following things:
1. The logo
2. The name of the product
3. The product is to help with the relief of Anxiety and Stress
4. Number of capsules the bottle contains
5. The back of the label should have
i) The ingredients
ii) Dosage
iii) Directions of use

Please use placeholder text where needed.

We look forward to seeing your design. Thank you.

```html
<!DOCTYPE html>
<html lang="en">
<head>
<meta charset="UTF-8">
<title>Vorna Health Sciences – Calm Drift Label</title>
<link href="https://fonts.googleapis.com/css2?family=Oswald:wght@500&family=Poppins:wght@400;500;600&display=swap" rel="stylesheet">
<style>
  :root {
    --page: #ffffff;
    --label: #f1ede3;
    --ink: #2b2b2b;
    --ink-soft: #4a4a4a;
    --plum: #a48a9b;
    --plum-line: #9c7f92;
    --rule: #b9b6b0;
    --leaf-green: #dfe6d9;
    --leaf-lilac: #e6dde3;
    --leaf-grey: #e2e0dc;
    --band-text: #f6f1f4;
  }
  * { margin: 0; padding: 0; box-sizing: border-box; }
  html, body {
    width: 1200px; height: 911px; overflow: hidden;
    background: var(--page);
    font-family: "Poppins", sans-serif;
    color: var(--ink);
  }
  .label-row { position: relative; width: 1200px; height: 911px; }
  .label {
    position: absolute; top: 338px;
    width: 320px; height: 380px;
    background: var(--label);
    overflow: hidden;
  }
  .label--one { left: 56px; }
  .label--two { left: 439px; }
  .label--three { left: 823px; }

  .brand {
    position: absolute; left: 54px; top: 44px;
    font-family: "Poppins", sans-serif;
    font-weight: 400; font-size: 22px; line-height: 1;
    color: var(--ink); white-space: nowrap;
  }

  .botanical {
    position: absolute; right: 0; top: 128px;
    width: 62px; height: 210px;
    border-radius: 30px 0 0 30px;
  }
  .label--one .botanical { background: linear-gradient(180deg, var(--leaf-green), rgba(241,237,227,0)); }
  .label--two .botanical { background: linear-gradient(180deg, var(--leaf-lilac), rgba(241,237,227,0)); }
  .label--three .botanical { top: 70px; height: 270px; background: linear-gradient(180deg, var(--leaf-grey), rgba(241,237,227,0)); }

  .product-name {
    position: absolute; left: 51px; top: 176px;
    font-family: "Oswald", sans-serif; font-weight: 500;
    font-size: 45px; line-height: 1; letter-spacing: 0.5px;
    text-transform: uppercase; color: var(--ink);
    white-space: nowrap;
  }
  .accent-rule {
    position: absolute; left: 54px; top: 238px;
    width: 109px; height: 2px; background: var(--plum-line);
  }
  .ingredient-types {
    position: absolute; left: 54px; top: 251px;
    font-size: 12.5px; letter-spacing: 0.6px; color: var(--ink-soft);
    white-space: nowrap;
  }
  .divider {
    position: absolute; left: 54px; top: 279px;
    width: 180px; height: 1px; background: var(--rule);
  }
  .benefit {
    position: absolute; left: 54px; top: 293px;
    font-size: 13px; letter-spacing: 1.2px; line-height: 21px;
    text-transform: uppercase; color: var(--ink-soft);
  }
  .benefit strong { font-weight: 600; color: var(--ink); }
  .benefit .and { font-weight: 500; }

  .info-band {
    position: absolute; left: 0; bottom: 0;
    width: 100%; height: 29px;
    background: var(--plum);
    display: flex; align-items: center;
    padding-left: 54px;
    font-size: 11.5px; letter-spacing: 1.1px;
    color: var(--band-text); text-transform: uppercase;
    white-space: nowrap;
  }
</style>
</head>
<body>
<main class="label-row">

  <section class="label label--one">
    <div class="brand">Vorna Health Sciences</div>
    <div class="botanical" role="img" aria-label="Soft green hand-drawn leafy sprig illustration"></div>
    <h1 class="product-name">Calm Drift</h1>
    <div class="accent-rule"></div>
    <p class="ingredient-types">Vitamins · Minerals · Herbs</p>
    <div class="divider"></div>
    <p class="benefit">Relief of<br><strong>Anxiety</strong> <span class="and">and</span> <strong>Stress</strong></p>
    <div class="info-band">60 Capsules | Dietary Supplement</div>
  </section>

  <section class="label label--two">
    <div class="brand">Vorna Health Sciences</div>
    <div class="botanical" role="img" aria-label="Lilac line-drawn leafy branch illustration"></div>
    <h1 class="product-name">Calm Drift</h1>
    <div class="accent-rule"></div>
    <p class="ingredient-types">Vitamins · Minerals · Herbs</p>
    <div class="divider"></div>
    <p class="benefit">Relief of<br><strong>Anxiety</strong> <span class="and">and</span> <strong>Stress</strong></p>
    <div class="info-band">60 Capsules | Dietary Supplement</div>
  </section>

  <section class="label label--three">
    <div class="brand">Vorna Health Sciences</div>
    <div class="botanical" role="img" aria-label="Grey line-drawn tall leafy stem illustration"></div>
    <h1 class="product-name">Calm Drift</h1>
    <div class="accent-rule"></div>
    <p class="ingredient-types">Vitamins · Minerals · Herbs</p>
    <div class="divider"></div>
    <p class="benefit">Relief of<br><strong>Anxiety</strong> <span class="and">and</span> <strong>Stress</strong></p>
    <div class="info-band">60 Capsules | Dietary Supplement</div>
  </section>

</main>
</body>
</html>
```